A start-up named "lumerova" - a clinical research organization needs a new PowerPoint design

We need a new PowerPoint Design (incl. business card and stationery design) for an early-stage start-up named "lumerova" seeking to build an ecosystem/ strategic partner alliances or consortium of committed and active collaborators to guide important components of the clinical trial.

Our ultimate goal is to avoid false neutrals – therapies that have not been and may never be evaluated in clinical trials due to the costs and/ or complexity.

The final design should highlight our patient-centric approach, innovative study design supported with the novel AI platform to make a stronger impact on patient lives.

Please see the attached brief for more details.
Updates

Requesting the proposals on color-coding, business-card designs, clinical research visuals, and icons as well as stationery design.

Target Market(s)

Pharma/ Biotech Executives
Medical Institutions
Clinical Trial Participants (Patients)

Colors
e34398

Requirements
Must have
• Use the Color Version of purple/ magenta logo

```html
<!DOCTYPE html>
<html lang="en">
<head>
<meta charset="utf-8">
<title>lumerova — Brand Identity</title>
<link href="https://fonts.googleapis.com/css2?family=Carlito:wght@400;700&display=swap" rel="stylesheet">
<style>
:root{
  --ink:#1c1b17;
  --plum:#821448;
  --berry:#ac1b60;
  --magenta:#e5097f;
  --pink:#e34398;
  --rose:#ea72b1;
  --blush:#f5b9d8;
  --silver:#d9d9d9;
  --text:#3a3a3a;
  --paper:#ffffff;
  --mist:#eceef1;
}
*{margin:0;padding:0;box-sizing:border-box}
html,body{width:1200px;height:4714px;overflow:hidden;background:var(--paper)}
body{position:relative;font-family:"Carlito",Calibri,Arial,sans-serif;color:var(--text)}
.wordmark{font-family:"Carlito",Calibri,Arial,sans-serif;font-weight:700;color:var(--berry);display:inline-flex;align-items:center;gap:.18em;letter-spacing:-.01em;line-height:1}
.wordmark .dot{width:.42em;height:.42em;background:var(--pink);display:inline-block}
.icon{width:1em;height:1em;fill:var(--pink);flex:none}

/* Colour slide */
.slide{position:absolute;left:110px;top:88px;width:982px;height:552px;background:var(--paper);box-shadow:0 10px 28px rgba(0,0,0,.14)}
.slide-title{position:absolute;left:40px;top:30px;font-size:40px;font-weight:700;color:var(--ink)}
.slide .wordmark{position:absolute;right:28px;top:28px;font-size:30px}
.swatch{position:absolute;width:66px;height:64px}
.swatch-label{position:absolute;font-size:17px;line-height:22px;color:var(--ink)}
.tint-bar{position:absolute;left:342px;width:305px;height:64px;display:flex;justify-content:space-between;align-items:center;padding:0 14px;color:#fff;font-weight:700;font-size:16px}
.theme-dialog{position:absolute;left:662px;top:110px;width:311px;height:316px;border:1px solid #c9c9c9;background:linear-gradient(#f7f7f7,#ececec)}
.slide-rule{position:absolute;left:0;right:0;bottom:0;height:6px;background:var(--magenta)}
.pager{position:absolute;right:12px;bottom:16px;display:flex;gap:8px;align-items:center;font-size:13px;color:var(--pink)}
.pager span.c{width:18px;height:18px;border:1.5px solid var(--pink);border-radius:50%;display:flex;align-items:center;justify-content:center;font-size:11px}

/* Business cards */
.card-stage{position:absolute;left:0;top:710px;width:1200px;height:1000px;background:var(--mist)}
.card{position:absolute;width:500px;height:286px;background:var(--paper);box-shadow:0 8px 24px rgba(0,0,0,.16)}
.card-front{left:70px;top:357px}
.card-front .wordmark{position:absolute;left:50%;top:50%;transform:translate(-50%,-50%);font-size:58px}
.card-back{left:630px;top:357px}
.card-name{position:absolute;left:36px;top:34px;font-size:28px;font-weight:700;color:var(--ink)}
.card-role{position:absolute;left:36px;top:68px;font-size:15px;color:var(--pink)}
.card-contacts{position:absolute;left:36px;top:120px;list-style:none;font-size:14px;color:var(--ink)}
.card-contacts li{display:flex;align-items:center;gap:10px;height:24px}
.card-back .wordmark{position:absolute;right:32px;bottom:34px;font-size:38px}

/* Letterhead */
.letterhead{position:absolute;left:104px;top:1789px;width:1014px;height:1317px;background:linear-gradient(#f4f5f7,#fafafb);box-shadow:0 16px 38px rgba(0,0,0,.22)}
.lh-header{position:absolute;left:0;top:0;width:100%;height:433px;background:linear-gradient(#e9ebee,#f0f1f3)}
.letterhead .wordmark{position:absolute;left:119px;top:240px;font-size:66px}
.contacts{position:absolute;list-style:none;color:var(--ink)}
.contacts li{display:flex;align-items:center}
.lh-contacts{left:666px;top:180px;font-size:19px}
.lh-contacts li{height:37px;gap:18px}
.lh-body{position:absolute;left:119px;top:462px;width:776px}
.lh-subject{font-size:40px;font-weight:400;color:var(--ink);margin-bottom:14px}
.lh-body p{font-size:17.2px;line-height:27.5px;text-align:justify;margin-bottom:14px}
.lh-sign{position:absolute;right:119px;top:1080px;text-align:right;font-size:19px;line-height:28px;color:var(--ink)}
.lh-sign .web{color:#666}

/* Envelope front */
.envelope{position:absolute;left:112px;top:3287px;width:1020px;height:527px;background:linear-gradient(100deg,#f8f8f9,#eeeff1);box-shadow:0 14px 32px rgba(0,0,0,.2)}
.envelope .wordmark{position:absolute;left:62px;top:95px;font-size:64px}
.env-contacts{left:62px;top:332px;font-size:14px}
.env-contacts li{height:31px;gap:16px}
.env-window{position:absolute;left:482px;top:258px;width:449px;height:195px;border-radius:14px;border:4px solid #d7d8db;background:linear-gradient(135deg,#e1e2e4,#c9cacd 55%,#dcdde0)}

/* Envelope back */
.envelope-back{position:absolute;left:115px;top:3929px;width:1021px;height:666px}
</style>
</head>
<body>
<svg width="0" height="0" style="position:absolute" aria-hidden="true">
  <symbol id="i-phone" viewBox="0 0 24 24"><path d="M6.6 2.5l3 3.4-1.8 2.6c1.2 2.8 3.4 5 6.2 6.2l2.6-1.8 3.4 3-1.6 3.2C11 18.6 5.4 13 4 3.9z"/></symbol>
  <symbol id="i-web" viewBox="0 0 24 24"><path d="M12 2a10 10 0 100 20 10 10 0 000-20zm0 2.2c.9 1.1 1.7 2.9 2 5H10c.3-2.1 1.1-3.9 2-5zM4.5 11h3.3c0 .7 0 1.4.1 2H4.5a7.6 7.6 0 010-2zm5.4 0h4.2c.1.7.1 1.3 0 2H9.9c-.1-.7-.1-1.3 0-2zm6.3 0h3.3a7.6 7.6 0 010 2h-3.4c.1-.6.1-1.3.1-2zM10 15h4c-.3 2.1-1.1 3.9-2 4.8-.9-.9-1.7-2.7-2-4.8z"/></symbol>
  <symbol id="i-mail" viewBox="0 0 24 24"><path d="M2 5h20v14H2zm2 2v.4l8 5.2 8-5.2V7z"/></symbol>
  <symbol id="i-pin" viewBox="0 0 24 24"><path d="M12 1.5a7 7 0 00-7 7c0 5 7 13 7 13s7-8 7-13a7 7 0 00-7-7zm0 4a3 3 0 110 6 3 3 0 010-6z"/></symbol>
</svg>

<section class="slide" aria-label="Colour coding slide">
  <h1 class="slide-title">Color Coding</h1>
  <span class="wordmark">lumerova<span class="dot"></span></span>

  <div class="swatch" style="left:62px;top:113px;background:var(--ink)"></div>
  <div class="swatch-label" style="left:161px;top:122px">#1c1b17<br>RGB – 28,27,23</div>
  <div class="swatch" style="left:62px;top:192px;background:var(--plum)"></div>
  <div class="swatch-label" style="left:161px;top:201px">#821448<br>RGB – 130,20,72</div>
  <div class="swatch" style="left:62px;top:271px;background:var(--berry)"></div>
  <div class="swatch-label" style="left:161px;top:280px">#ac1b60<br>RGB – 172,27,96</div>
  <div class="swatch" style="left:62px;top:350px;background:var(--magenta)"></div>
  <div class="swatch-label" style="left:161px;top:359px">#e5097f<br>RGB – 229,09,127</div>
  <div class="swatch" style="left:62px;top:429px;background:var(--pink)"></div>
  <div class="swatch-label" style="left:161px;top:438px">#e34398<br>RGB – 227,67,152</div>

  <div class="swatch" style="left:342px;top:113px;background:var(--rose)"></div>
  <div class="swatch-label" style="left:441px;top:122px">#ea72b1<br>RGB – 234,114,177</div>
  <div class="swatch" style="left:342px;top:192px;background:var(--blush)"></div>
  <div class="swatch-label" style="left:441px;top:201px">#f5b9d8<br>RGB – 245,185,216</div>
  <div class="swatch" style="left:342px;top:271px;background:var(--silver)"></div>
  <div class="swatch-label" style="left:441px;top:280px">#d9d9d9<br>RGB – 217,217,217</div>

  <div class="tint-bar" style="top:350px;background:linear-gradient(90deg,var(--magenta),var(--plum))"><span>0%</span><span>0%</span></div>
  <div class="tint-bar" style="top:429px;background:var(--pink)"><span>14%</span><span>14%</span></div>

  <div class="theme-dialog" role="img" aria-label="Screenshot of the theme colour settings dialog"></div>

  <div class="pager"><span class="c">&lt;</span>21<span class="c">&gt;</span></div>
  <div class="slide-rule"></div>
</section>

<section class="card-stage" aria-label="Business cards">
  <div class="card card-front">
    <span class="wordmark">lumerova<span class="dot"></span></span>
  </div>
  <div class="card card-back">
    <div class="card-name">Name Here</div>
    <div class="card-role">Job Position</div>
    <ul class="card-contacts">
      <li><svg class="icon"><use href="#i-phone"/></svg>+1 234 567 890</li>
      <li><svg class="icon"><use href="#i-web"/></svg>www.yourwebsite.com</li>
      <li><svg class="icon"><use href="#i-mail"/></svg>addyouremail@here.com</li>
      <li><svg class="icon"><use href="#i-pin"/></svg>Add your location here</li>
    </ul>
    <span class="wordmark">lumerova<span class="dot"></span></span>
  </div>
</section>

<section class="letterhead" aria-label="Letterhead">
  <div class="lh-header"></div>
  <span class="wordmark">lumerova<span class="dot"></span></span>
  <ul class="contacts lh-contacts">
    <li><svg class="icon"><use href="#i-phone"/></svg>+1 234 567 890</li>
    <li><svg class="icon"><use href="#i-web"/></svg>www.yourwebsite.com</li>
    <li><svg class="icon"><use href="#i-mail"/></svg>addyouremail@here.com</li>
    <li><svg class="icon"><use href="#i-pin"/></svg>Add your location here</li>
  </ul>
  <div class="lh-body">
    <h2 class="lh-subject">Subject Headline Here</h2>
    <p>Lorem ipsum dolor sit amet, consectetuer adipiscing elit, sed diam nonummy nibh euismod tincidunt ut laoreet dolore magna aliquam erat volutpat. Ut wisi enim ad minim veniam, quis nostrud exerci tation ullamcorper suscipit lobortis nisl ut aliquip ex ea commodo consequat. Duis autem vel eum iriure dolor in hendrerit in vulputate velit esse molestie consequat, vel illum dolore eu feugiat nulla facilisis at vero eros et accumsan et iusto odio dignissim qui blandit praesent luptatum zzril delenit augue duis dolore te feugait nulla facilisi.</p>
    <p>Porem ipsum dolor sit amet, cons ectetuer adipiscing elit, sed diam nonummy nibh euismod tincidunt ut laoreet dolore magna aliquam erat volutpat. Ut wisi enim ad minim veniam, quis nostrud exerci tation.</p>
    <p>Lorem ipsum dolor sit amet, cons ectetuer adipiscing elit, sed diam nonummy nibh euismod tincidunt ut laoreet dolore magna aliquam erat volutpat. Ut wisi enim ad minim veniam, quis nostrud exerci tation ullamcorper suscipit lobortis nisl ut aliquip ex ea commodo consequat. Lorem ipsum dolor sit amet, cons ectetuer adipiscing elit, sed diam nonummy nibh euismod tincidunt ut laoreet dolore</p>
  </div>
  <div class="lh-sign">
    Add your name and position here<br>
    Lorem ipsum dolor sit amet<br>
    <span class="web">www.yourwebsite.com</span>
  </div>
</section>

<section class="envelope" aria-label="Envelope front">
  <span class="wordmark">lumerova<span class="dot"></span></span>
  <ul class="contacts env-contacts">
    <li><svg class="icon"><use href="#i-phone"/></svg>+1 234 567 890</li>
    <li><svg class="icon"><use href="#i-web"/></svg>www.yourwebsite.com</li>
    <li><svg class="icon"><use href="#i-mail"/></svg>addyouremail@here.com</li>
    <li><svg class="icon"><use href="#i-pin"/></svg>Add your location here</li>
  </ul>
  <div class="env-window"></div>
</section>

<svg class="envelope-back" viewBox="0 0 1021 666" aria-label="Envelope back">
  <defs>
    <linearGradient id="flap" x1="0" y1="0" x2="0" y2="1">
      <stop offset="0" stop-color="#ececee"/><stop offset="1" stop-color="#d4d5d8"/>
    </linearGradient>
    <linearGradient id="body" x1="0" y1="0" x2="1" y2="1">
      <stop offset="0" stop-color="#fafafa"/><stop offset="1" stop-color="#eeeff1"/>
    </linearGradient>
    <filter id="shadow" x="-5%" y="-5%" width="110%" height="115%"><feDropShadow dx="0" dy="10" stdDeviation="12" flood-opacity=".2"/></filter>
  </defs>
  <rect x="0" y="141" width="1021" height="510" fill="url(#body)" filter="url(#shadow)"/>
  <path d="M0,141 L31,30 Q40,0 70,0 L951,0 Q981,0 990,30 L1021,141 L960,260 Q945,287 915,287 L106,287 Q76,287 61,260 Z" fill="url(#flap)"/>
</svg>
</body>
</html>
```